Tech business card design

We need an amazing business card design for our new business 'Pexla' a marketing tech startup based in Sydney, Australia. We provide an online marketplace for businesses to search and buy advertising media, connect with service providers and learn more about marketing. We wish to communicate 'cool tech', reliability and professionalism and design based around our logo.

Target Market(s)

Business Owners

Contact Information for Business Card

Name
Position
Email Address
Website
Phone Number

Font styles to use
Other font styles liked:
• Avenir & Avenir Next

Colors

Designer to choose colors to be used in the design.

```html
<!DOCTYPE html>
<html lang="en">
<head>
<meta charset="utf-8">
<title>Pexla Business Card</title>
<link href="https://fonts.googleapis.com/css2?family=Mulish:wght@400;700;800&display=swap" rel="stylesheet">
<style>
  :root {
    --navy: #141540;
    --white: #ffffff;
    --backdrop: #b4b4b4;
    --ink-soft: #3a3b5c;
  }
  * { margin: 0; padding: 0; box-sizing: border-box; }
  html, body {
    width: 1200px;
    height: 930px;
    overflow: hidden;
    background: var(--backdrop);
    font-family: "Mulish", "Avenir Next", Arial, sans-serif;
  }
  .stage { position: relative; width: 1200px; height: 930px; }
  .card {
    position: absolute;
    width: 560px;
    height: 320px;
    border-radius: 22px;
    overflow: hidden;
    box-shadow: 0 10px 24px rgba(0,0,0,0.25);
  }
  .card-back {
    left: 90px;
    top: 110px;
    background: var(--navy);
    display: flex;
    align-items: center;
    justify-content: center;
  }
  .wordmark {
    font-weight: 800;
    font-size: 96px;
    letter-spacing: -2px;
    line-height: 1;
    color: var(--white);
  }
  .wordmark .tm {
    font-size: 14px;
    font-weight: 800;
    letter-spacing: 0;
    margin-left: 6px;
    vertical-align: baseline;
  }
  .card-front {
    left: 550px;
    top: 500px;
    background: var(--white);
  }
  .card-front .wave { position: absolute; inset: 0; }
  .card-front .wordmark {
    position: absolute;
    left: 34px;
    top: 112px;
    font-size: 82px;
    color: var(--navy);
  }
  .holder {
    position: absolute;
    right: 30px;
    top: 24px;
    text-align: right;
    color: var(--navy);
  }
  .holder-name { font-weight: 700; font-size: 20px; }
  .holder-role { font-size: 12px; color: var(--ink-soft); margin-top: 2px; }
  .contact {
    position: absolute;
    right: 24px;
    top: 160px;
    text-align: right;
    color: var(--white);
    font-size: 13px;
    line-height: 1.45;
  }
  .contact .address { margin-bottom: 10px; }
  .contact-line { display: flex; align-items: center; justify-content: flex-end; gap: 7px; }
  .contact-line svg { width: 11px; height: 11px; flex: none; }
</style>
</head>
<body>
<div class="stage">

  <section class="card card-back" aria-label="Card back">
    <div class="wordmark">Pexla<span class="tm">TM</span></div>
  </section>

  <section class="card card-front" aria-label="Card front">
    <svg class="wave" viewBox="0 0 560 320" preserveAspectRatio="none" aria-hidden="true">
      <path d="M560 84 C440 84 385 100 355 160 C325 225 255 262 0 290 L0 320 L560 320 Z" fill="var(--navy)"/>
      <path d="M560 70 C432 70 372 88 340 150 C308 214 240 252 70 276" fill="none" stroke="var(--navy)" stroke-width="5"/>
      <path d="M560 100 C448 100 400 116 372 174 C342 238 270 276 0 304" fill="none" stroke="var(--white)" stroke-width="4"/>
    </svg>

    <div class="wordmark">Pexla<span class="tm">TM</span></div>

    <div class="holder">
      <div class="holder-name">Daniel Reyes</div>
      <div class="holder-role">Director</div>
    </div>

    <div class="contact">
      <div class="address">1820 Harbour Lane<br>Sydney, NSW 2000</div>
      <div class="contact-line">+61 2 5550 1947
        <svg viewBox="0 0 12 12" aria-hidden="true"><path d="M2.5 1 L4.5 1 L5.2 3.5 L4 4.5 C4.6 6 6 7.4 7.5 8 L8.5 6.8 L11 7.5 L11 9.5 C11 10.3 10.3 11 9.5 11 C5 11 1 7 1 2.5 C1 1.7 1.7 1 2.5 1 Z" fill="var(--white)"/></svg>
      </div>
      <div class="contact-line">info@pexla.com
        <svg viewBox="0 0 12 12" aria-hidden="true"><rect x="1" y="2.5" width="10" height="7" fill="none" stroke="var(--white)" stroke-width="1.2"/><path d="M1 2.5 L6 6.5 L11 2.5" fill="none" stroke="var(--white)" stroke-width="1.2"/></svg>
      </div>
      <div class="contact-line">www.pexla.com
        <svg viewBox="0 0 12 12" aria-hidden="true"><circle cx="6" cy="6" r="5" fill="none" stroke="var(--white)" stroke-width="1.1"/><ellipse cx="6" cy="6" rx="2.2" ry="5" fill="none" stroke="var(--white)" stroke-width="1"/><path d="M1 6 H11" stroke="var(--white)" stroke-width="1"/></svg>
      </div>
    </div>
  </section>

</div>
</body>
</html>
```